Buch-/eBook-Cover für Traumatherapeutin
Zielgruppe
Ich bin Traumatherapeutin und schreibe ein Buch zum Thema Trauma bearbeiten.
Meine Zielgruppe sucht Heilung, Genesung, Selbstliebe etc.
Aufgabenstellung
Buchcover
Bitte erstell mir ein modernes positives inspirierendes Buchcover mit dem
Titel: 'Morgenlicht NEU entdecken“
Untertitel: „Spüre den Mut der ganz in dir wohnt“
Dr. Mira Kessow
Ich hätte gerne ein modernes Buch, das entweder einen Bezug zum Thema Trauma hat oder aber einfach stylische Schriftzüge. Bin aber auch offen für andere Vorschläge.
Dunkelblau, weiß und türkis oder auch rosa mag ich ganz gerne. Wobei Dunkelblau, weiß und türkis meine Favoriten sind und mit rosa höchstens kleinere Akzente gesetzt werden sollten.
Das Buchcover soll modern sein und direkt ansprechen. Gerne eine originelle Lösung, oder etwas Besonderes, etwas das Tiefe ausdrückt, oder man mehrmals hinsehen muss um etwas zu erkennen oder etwas das mehr Interpretationsspielraum lässt.
Gerne auch viel weiß, zumindest heller und nicht zu dunkel. Stylish, aber nicht überfrachtet.
Schreib mich gerne an, wenn du Fragen hast.
Ich habe mal zwei Beispiel von Typolösungen angehängt, die ich ganz cool fände.
Ich freue mich auf deine Ideen :-)
Ganz liebe Grüße
Mira

```html
<!DOCTYPE html>
<html lang="de">
<head>
<meta charset="utf-8">
<title>Morgenlicht NEU entdecken – Buchcover</title>
<link rel="stylesheet" href="https://fonts.googleapis.com/css2?family=Montserrat:wght@600;700;800&display=swap">
<style>
  :root {
    --paper: #f2f1f2;
    --navy: #21446d;
    --teal: #45c2b8;
    --wash-light: #dcefed;
    --wash-mid: #a9dcd8;
    --wash-deep: #86cbc9;
  }
  * { margin: 0; padding: 0; box-sizing: border-box; }
  html, body {
    width: 668px;
    height: 1200px;
    overflow: hidden;
    background: var(--paper);
  }
  .cover {
    position: relative;
    width: 668px;
    height: 1200px;
    background: var(--paper);
    font-family: "Montserrat", Arial, sans-serif;
    color: var(--navy);
    overflow: hidden;
  }
  .top-curve {
    position: absolute;
    left: 0;
    top: 0;
    width: 668px;
    height: 160px;
  }
  .author {
    position: absolute;
    top: 116px;
    left: 0;
    width: 100%;
    text-align: center;
    font-weight: 700;
    font-size: 27px;
    letter-spacing: 0.12em;
    color: var(--navy);
  }
  .title {
    position: absolute;
    left: 40px;
    top: 196px;
    width: 600px;
    font-weight: 800;
    line-height: 1;
  }
  .title-line { display: block; }
  .title-line--first {
    font-size: 91px;
    letter-spacing: -0.025em;
    color: var(--navy);
  }
  .title-line--accent {
    font-size: 150px;
    letter-spacing: -0.01em;
    color: var(--teal);
    margin-top: 4px;
  }
  .title-line--last {
    font-size: 104px;
    letter-spacing: -0.02em;
    color: var(--navy);
    margin-top: 2px;
  }
  .subtitle {
    position: absolute;
    left: 46px;
    top: 640px;
    font-weight: 600;
    font-size: 33px;
    line-height: 1.45;
    color: var(--navy);
  }
  .illustration {
    position: absolute;
    left: 0;
    top: 600px;
    width: 668px;
    height: 600px;
  }
</style>
</head>
<body>
  <main class="cover">
    <svg class="top-curve" viewBox="0 0 668 160" aria-hidden="true">
      <path d="M0,128 C60,88 140,72 220,66 C300,60 340,30 378,0" fill="none" stroke="var(--teal)" stroke-width="3" stroke-linecap="round"/>
    </svg>

    <p class="author">DR. MIRA KESSOW</p>

    <h1 class="title">
      <span class="title-line title-line--first">Morgenlicht</span>
      <span class="title-line title-line--accent">NEU</span>
      <span class="title-line title-line--last">entdecken</span>
    </h1>

    <p class="subtitle">Spüre den Mut<br>der ganz<br>in dir wohnt</p>

    <svg class="illustration" viewBox="0 0 668 600" role="img" aria-label="Türkise Linienzeichnung einer tanzenden Frau mit blütenförmigen Ballons über einer sanften türkisen Aquarellfläche">
      <defs>
        <linearGradient id="wash" x1="0" y1="0" x2="0" y2="1">
          <stop offset="0" stop-color="var(--wash-light)"/>
          <stop offset="0.5" stop-color="var(--wash-mid)"/>
          <stop offset="1" stop-color="var(--wash-deep)"/>
        </linearGradient>
        <radialGradient id="figure-glow" cx="0.5" cy="0.5" r="0.5">
          <stop offset="0" stop-color="var(--wash-mid)" stop-opacity="0.55"/>
          <stop offset="1" stop-color="var(--wash-mid)" stop-opacity="0"/>
        </radialGradient>
      </defs>
      <path d="M0,300 C80,260 150,270 230,300 C320,330 380,250 460,240 C540,230 600,260 668,250 L668,600 L0,600 Z" fill="url(#wash)"/>
      <ellipse cx="500" cy="220" rx="170" ry="230" fill="url(#figure-glow)"/>
    </svg>
  </main>
</body>
</html>
```